RW Framewell Inc Business cards

We need business cards using our existing logo but slightly modified. Right now the logo says RW Loadbearing Masonry. We want to keep the RW part of the design, but replace the Structural Concrete portion with "FRAMEWELL". Please see the attached file.
Ideally this would be a blank template so we can add Different Names, titles, and phone numbers later.
On the one side we want only the logo and on the other side the detail. I'm attaching an example for you to see.
Please reach out with any other questions. Our address and other details will be given out once we find a design we like.

Target Market(s)

Construction Industry

```html
<!DOCTYPE html>
<html lang="en">
<head>
<meta charset="utf-8">
<title>RW Framewell Inc – Business Cards</title>
<link rel="stylesheet" href="https://fonts.googleapis.com/css2?family=Montserrat:wght@600&family=Roboto:wght@400;500&display=swap">
<style>
  :root {
    --page-bg: #3a3a3d;
    --card-dark: #1f1f22;
    --brand-blue: #2f67b1;
    --front-logo: #5c5d62;
    --text-light: #ffffff;
  }
  * { box-sizing: border-box; margin: 0; padding: 0; }
  html, body {
    width: 799px;
    height: 1200px;
    overflow: hidden;
    background: var(--page-bg);
  }
  .sheet { position: relative; width: 799px; height: 1200px; }
  .card {
    position: absolute;
    left: 90px;
    width: 620px;
    height: 354px;
    background: var(--card-dark);
    border-radius: 4px;
    overflow: hidden;
    box-shadow: 0 10px 28px rgba(0,0,0,0.45);
  }
  .card--front { top: 140px; }
  .card--back  { top: 706px; }

  .wordmark {
    font-family: "Montserrat", sans-serif;
    font-weight: 600;
    letter-spacing: 0.12em;
    white-space: nowrap;
  }
  .card--front .wordmark {
    position: absolute;
    left: 0; right: 0;
    top: 150px;
    text-align: center;
    font-size: 46px;
    color: var(--front-logo);
  }
  .card--back .wordmark {
    position: absolute;
    left: 40px;
    top: 62px;
    font-size: 30px;
    color: var(--text-light);
  }

  .accent-band {
    position: absolute;
    left: 0; right: 0; bottom: 0;
    height: 160px;
    background: linear-gradient(180deg, rgba(47,103,177,0) 0%, rgba(47,103,177,0.55) 35%, var(--brand-blue) 70%);
  }

  .person {
    position: absolute;
    right: 36px;
    top: 92px;
    text-align: right;
    font-family: "Roboto", sans-serif;
    color: var(--text-light);
  }
  .person__name { font-weight: 500; font-size: 20px; color: var(--brand-blue); }
  .person__title { font-size: 15px; margin-top: 2px; }
  .person__address { font-size: 15px; line-height: 1.3; margin-top: 12px; }

  .contacts {
    position: absolute;
    right: 36px;
    bottom: 26px;
    list-style: none;
    font-family: "Roboto", sans-serif;
    font-size: 16px;
    color: var(--text-light);
    text-align: right;
  }
  .contacts li {
    display: flex;
    justify-content: flex-end;
    align-items: center;
    gap: 8px;
    line-height: 1.45;
  }
  .contacts svg { width: 14px; height: 14px; fill: var(--text-light); }
</style>
</head>
<body>
<main class="sheet">

  <section class="card card--front" aria-label="Card front">
    <div class="wordmark">RW FRAMEWELL</div>
  </section>

  <section class="card card--back" aria-label="Card back">
    <div class="accent-band" role="img" aria-label="Decorative blue and grey wave band"></div>

    <div class="wordmark">RW FRAMEWELL</div>

    <div class="person">
      <p class="person__name">Dana RW Morgan</p>
      <p class="person__title">Managing Director</p>
      <p class="person__address">418 Sample Ave., Any Town,<br>Oregon, US 975310</p>
    </div>

    <ul class="contacts">
      <li>555-204-3170
        <svg viewBox="0 0 16 16"><path d="M3 1h3l1.5 4-2 1.2a8 8 0 0 0 4.3 4.3L11 8.5l4 1.5v3a2 2 0 0 1-2 2A12 12 0 0 1 1 3a2 2 0 0 1 2-2z"/></svg>
      </li>
      <li>examplesite.com
        <svg viewBox="0 0 16 16"><path d="M1 3h14v10H1z M2 4l6 5 6-5" fill="none" stroke="#fff" stroke-width="1.5"/></svg>
      </li>
      <li>dana@examplesite.com
        <svg viewBox="0 0 16 16"><circle cx="8" cy="8" r="6.5" fill="none" stroke="#fff" stroke-width="1.3"/><path d="M1.5 8h13M8 1.5c-3 3.5-3 9.5 0 13M8 1.5c3 3.5 3 9.5 0 13" fill="none" stroke="#fff" stroke-width="1.1"/></svg>
      </li>
    </ul>
  </section>

</main>
</body>
</html>
```